Motor Oil Lubricant Package Labels

We are looking for a logo and label that we can put on our motor oil bottle 1 liter and 5 liter. The name of our motor oil is Corvana. We want to design our flagship logo for CORVANA MOTOR OILS and as well as the label that will go on the bottle. We have some drafts that we have come up with attached and would like to see more options. The concept of a timeless motor oil and the endless loop of lubricating oils incorporated in the design. We will have full synthetic motor oil, a synthetic blend motor, ATF III transmission fluid, KRL-VI transmission fluid. hydraulic oils etc. Examples will be attached
Target Market(s)
Automotive Lubricants and Chemicals
Industry/Entity Type
Automotive
Logo Text
Corvana Lubricants
Font styles to use
Other font styles liked:
- Let designer choose
Requirements
Must have
- The Corvana sign incorporated in a very cool way to our name. Our brand needs to stick out
Nice to have
- Automotive lubricant related and colors red, white, and blue incorporated in the design
Should not have
- Images of individuals and or topics not related to automotive lubricants.

```html
<!DOCTYPE html>
<html lang="en">
<head>
<meta charset="utf-8">
<title>Corvana Motor Oil – 5W-30 Synthetic Blend Label</title>
<link href="https://fonts.googleapis.com/css2?family=Roboto+Condensed:wght@400;700&family=Oswald:wght@600;700&family=Russo+One&display=swap" rel="stylesheet">
<style>
  :root{
    --brand-blue:#2b4fa8;
    --brand-red:#e31e25;
    --ink:#2a2a2a;
    --white:#ffffff;
    --gold:#c99a2e;
    --gold-light:#f3d27a;
    --silver-dark:#9ea3a8;
    --silver-light:#eef0f2;
  }
  *{box-sizing:border-box;margin:0;padding:0}
  html,body{width:1200px;height:864px;overflow:hidden;background:var(--white)}
  .canvas{position:relative;width:1200px;height:864px;background:var(--white)}
  .canvas-frame{position:absolute;inset:14px 2px 2px 2px;border:1px solid #d6d6d6}
  .label{
    position:absolute;top:60px;width:468px;height:757px;border-radius:40px;overflow:hidden;
    background:
      repeating-linear-gradient(0deg,rgba(255,255,255,.08) 0 1px,rgba(0,0,0,.04) 1px 3px),
      linear-gradient(100deg,var(--silver-dark) 0%,var(--silver-light) 28%,#b4b8bc 48%,#f3f4f5 68%,#a8acb0 100%);
    font-family:"Roboto Condensed",sans-serif;color:var(--ink);
  }
  .label--front{left:104px}
  .label--back{left:627px}
  .layer{position:absolute;inset:0;width:100%;height:100%}
  .abs{position:absolute;white-space:nowrap}

  .brand-name{font-weight:700;color:var(--brand-blue);letter-spacing:1px;line-height:1}
  .brand-sub{font-weight:700;color:var(--ink);letter-spacing:1px;line-height:1}
  .brand-dot{position:absolute;border-radius:50%;background:var(--brand-red)}

  .tag-advanced{font-family:"Russo One",sans-serif;color:var(--brand-blue);line-height:1;text-align:center}
  .tag-performance{font-family:"Russo One",sans-serif;color:var(--white);background:var(--brand-red);text-align:center}
  .tag-tagline{font-family:"Russo One",sans-serif;font-size:11px;color:var(--ink);text-align:center;line-height:16px;letter-spacing:.6px}

  .badge{position:absolute;border-radius:50%;
    background:radial-gradient(circle at 40% 35%,var(--gold-light),var(--gold) 70%,#8a6418);
    box-shadow:0 2px 6px rgba(0,0,0,.3)}
  .badge::after{content:"";position:absolute;inset:14%;border-radius:50%;background:#f7f4ec;box-shadow:inset 0 0 0 2px var(--gold)}

  .grade-text{font-family:"Roboto Condensed",sans-serif;font-weight:700;fill:var(--white)}
  .grade-mini{font-family:"Oswald",sans-serif;font-weight:600;fill:var(--white)}
  .grade-num{font-family:"Oswald",sans-serif;font-weight:700;fill:var(--white);stroke:var(--brand-blue);stroke-width:2.5;paint-order:stroke fill}

  .volume{font-weight:700;font-size:27px;color:var(--ink);line-height:1}
  .made-usa{font-weight:700;font-size:21px;color:var(--white);text-align:center;line-height:1}
  .made-usa__stars{font-size:10px;letter-spacing:3px;display:block;margin-top:2px}

  .body-copy{font-size:15.6px;line-height:20.4px;text-align:justify;color:var(--ink);white-space:normal}
  .body-copy b{font-weight:700}
  .hl-red{color:var(--brand-red)}
  .hl-blue{color:var(--brand-blue)}
  .hl-blue-bold{color:var(--brand-blue);font-weight:700}
  .benefits{list-style:none;color:var(--brand-blue);font-size:15.6px;line-height:20.4px;font-weight:700}
  .benefits li{position:relative;padding-left:41px}
  .benefits li::before{content:"•";position:absolute;left:0}

  .small-copy{font-size:12.5px;line-height:16.3px;text-align:justify;color:var(--ink);white-space:normal}
  .small-copy .head{font-weight:700;font-size:13px}

  .sus{font-family:"Oswald",sans-serif;font-weight:700;font-size:24px;color:var(--white);line-height:1;letter-spacing:.5px}
  .sus-box{background:var(--white)}
  .flag{overflow:hidden;background:repeating-linear-gradient(180deg,var(--brand-red) 0 4px,var(--white) 4px 8px)}
  .flag__canton{position:absolute;left:0;top:0;width:42%;height:54%;background:var(--brand-blue)}
  .made-box{background:var(--white);border:1px solid var(--ink);font-size:14px;text-align:center;line-height:16px;letter-spacing:1px}
</style>
</head>
<body>
<div class="canvas">
  <div class="canvas-frame"></div>

  <!-- FRONT LABEL -->
  <section class="label label--front">
    <svg class="layer" viewBox="0 0 468 757" aria-hidden="true">
      <path d="M140,0 L468,0 L468,92 C380,70 260,35 140,0 Z" fill="var(--brand-red)"/>
      <path d="M330,0 L468,0 L468,58 C420,40 370,20 330,0 Z" fill="var(--brand-blue)"/>
      <path d="M468,78 C400,140 340,230 300,320 C255,410 205,470 192,570 C185,640 188,690 205,715 C218,735 235,750 250,757 L468,757 Z" fill="var(--brand-red)"/>
      <path d="M468,108 C415,165 365,245 325,330 C290,410 238,460 228,555 C222,620 235,660 265,678 C330,700 400,706 468,704 Z" fill="var(--brand-blue)"/>
    </svg>

    <div class="brand-dot" style="left:62px;top:150px;width:22px;height:22px"></div>
    <div class="abs brand-name" style="left:64px;top:176px;font-size:60px">CORVANA</div>
    <div class="abs brand-sub" style="left:193px;top:233px;font-size:18px">MOTOR OIL</div>

    <div class="abs tag-advanced" style="left:80px;top:304px;width:192px;font-size:20px">MOST ADVANCED</div>
    <div class="abs tag-performance" style="left:90px;top:328px;width:174px;height:21px;font-size:17px;line-height:21px">PERFORMANCE</div>
    <div class="abs tag-tagline" style="left:86px;top:356px;width:180px">MAXIMUM PROTECTION<br>FOR MORE MILES</div>

    <div class="badge" role="img" aria-label="Certification seal" style="left:26px;top:499px;width:102px;height:102px"></div>

    <svg class="layer" viewBox="0 0 468 757">
      <text class="grade-text" x="341" y="364" font-size="38" textLength="76" lengthAdjust="spacingAndGlyphs">SAE</text>
      <text class="grade-text" transform="translate(341,370) rotate(90)" font-size="108" textLength="268" lengthAdjust="spacingAndGlyphs">5W-30</text>
      <text class="grade-text" transform="translate(428,483) rotate(90)" font-size="17" textLength="153" lengthAdjust="spacingAndGlyphs">SYNTHETIC BLEND</text>
      <text class="grade-text" transform="translate(306,541) rotate(90)" font-size="30" textLength="91" lengthAdjust="spacingAndGlyphs">ALI SN</text>
    </svg>

    <div class="abs volume" style="left:35px;top:700px">32oz 1946mU</div>
    <div class="abs made-usa" style="left:214px;top:700px;width:118px">Made In USA<span class="made-usa__stars">★★★</span></div>
  </section>

  <!-- BACK LABEL -->
  <section class="label label--back">
    <svg class="layer" viewBox="0 0 468 757" aria-hidden="true">
      <path d="M180,0 L468,0 L468,100 C370,85 260,45 180,0 Z" fill="var(--brand-red)"/>
      <path d="M330,0 L468,0 L468,62 C420,50 375,28 330,0 Z" fill="var(--brand-blue)"/>
      <rect x="49" y="108" width="12" height="36" fill="var(--brand-blue)"/>
      <text class="grade-mini" transform="translate(58.5,141) rotate(-90)" font-size="10" textLength="30" lengthAdjust="spacingAndGlyphs">SAE</text>
      <rect x="106" y="102" width="62" height="8" fill="var(--brand-blue)"/>
      <text class="grade-mini" x="109" y="108.5" font-size="6.5" textLength="56" lengthAdjust="spacingAndGlyphs">SYNTHETIC BLEND</text>
      <text class="grade-num" x="64" y="142" font-size="40" textLength="106" lengthAdjust="spacingAndGlyphs">5W-30</text>
      <rect x="128" y="144" width="36" height="10" fill="var(--brand-blue)"/>
      <text class="grade-mini" x="132" y="152" font-size="8" textLength="28" lengthAdjust="spacingAndGlyphs">ALI SN</text>
    </svg>

    <div class="brand-dot" style="left:80px;top:30px;width:14px;height:14px"></div>
    <div class="abs brand-name" style="left:47px;top:52px;font-size:33px">CORVANA</div>
    <div class="abs brand-sub" style="left:112px;top:81px;font-size:9.5px">MOTOR OIL</div>

    <div class="abs tag-advanced" style="left:200px;top:116px;width:130px;font-size:13.5px">MOST ADVANCED</div>
    <div class="abs tag-performance" style="left:206px;top:133px;width:116px;height:16px;font-size:11.5px;line-height:16px">PERFORMANCE</div>

    <div class="badge" role="img" aria-label="Certification seal" style="left:351px;top:72px;width:78px;height:78px"></div>

    <div class="abs" style="left:16px;top:162px;width:435px;white-space:normal">
      <p class="body-copy"><span class="hl-red">CORVANA MOTOR OIL</span> <span class="hl-blue">5W30 and SAE</span> <b>Synthetic Blend Motor Oil provides the ultimate performance and protection, especially under severe driving conditions.</b> It utilized newly developed additive technology to achieve among the lowest retes of wear ever for motor oils, well exceeding the most stringent North American specifications for wear control, cleanliness and sludge, oxidation control, and emission system and seal compatibility, while meeting the standards for fuel economy.</p>
      <p class="body-copy"><span class="hl-blue-bold">Licensed ILMAC GF-5 and ALI SN</span> “Resource Conserving” by the Allied Lubricant Institute (ALI) as all previous service classification. It is compatible with all conventional and synthetic oils.</p>
      <ul class="benefits">
        <li>Provides Protections That Conventional Oils Can’t</li>
        <li>Won’t Break Down Under Extreme Temperature</li>
        <li>Superior Protection For Extended Service Intervals.</li>
      </ul>
    </div>

    <p class="abs small-copy" style="left:16px;top:462px;width:324px"><span class="hl-red">CORVANA MOTOR OIL</span> is manufactured to stringent standards. Every batch is tested, from raw materials to finished product, to insure you’re getting the Best Protection and Highest Performance from every quart.</p>

    <p class="abs small-copy" style="left:16px;top:543px;width:324px"><span class="head">WARNING! AVOID SKIN CONTACT WITH USED MOTOR OIL!</span><br>Used moter oils have caused skin cancer in laboratory, animals when repeatedly applied and left in place between applications, In case of skin contact promptly wash thoroughly with soap and water, Oil soild clothing should be cleand before reuse</p>

    <p class="abs small-copy" style="left:16px;top:642px;width:324px;text-align:left">DON’T POLLUTE! Conserve resources<br>Take used oil to collection center.</p>

    <div class="abs sus" style="left:360px;top:456px">SUS 350</div>
    <div class="abs sus-box" style="left:351px;top:484px;width:100px;height:173px"></div>
    <div class="abs flag" style="left:351px;top:664px;width:100px;height:51px"><span class="flag__canton"></span></div>
    <div class="abs made-box" style="left:351px;top:716px;width:100px;height:18px">MADE IN USA</div>
  </section>
</div>
</body>
</html>
```